KOVA! Card

The single side "business card" will be utilized to write down product information for our customers. The card needs to include our logo in josefin font and read KOVA! on the front. Our brand colors are espresso brown and copper. The back needs to be white (blank) to allow us to write information down. We want modern, bold, clean and fun.
I have attached a copy of our logo but you do not have to utilize exactly as shown.

```html
<!DOCTYPE html>
<html lang="en">
<head>
<meta charset="utf-8">
<title>KOVA! Card</title>
<link rel="stylesheet" href="https://fonts.googleapis.com/css2?family=Josefin+Sans:wght@300;400;600&display=swap">
<style>
  :root {
    --espresso: #2a1811;
    --copper: #c0622a;
    --backdrop: #e9e8ec;
  }
  * { margin: 0; padding: 0; box-sizing: border-box; }
  html, body {
    width: 1200px;
    height: 900px;
    overflow: hidden;
    background: var(--backdrop);
  }
  .card {
    position: absolute;
    left: 110px;
    top: 173px;
    width: 980px;
    height: 554px;
    background: var(--espresso);
    overflow: hidden;
    font-family: "Josefin Sans", sans-serif;
    color: var(--copper);
  }
  .brand {
    position: absolute;
    right: 48px;
    top: 52px;
    text-align: right;
  }
  .brand-name {
    font-size: 54px;
    font-weight: 400;
    letter-spacing: 2px;
    line-height: 1;
  }
  .brand-tagline {
    font-size: 20px;
    font-weight: 300;
    letter-spacing: 4px;
    text-transform: uppercase;
    line-height: 1;
    margin-top: 12px;
  }
  .wordmark {
    position: absolute;
    inset: 0;
    width: 980px;
    height: 554px;
  }
  .wordmark-text {
    font-family: "Josefin Sans", sans-serif;
    font-weight: 600;
    font-size: 230px;
    fill: var(--copper);
  }
  .accent { fill: var(--copper); }
</style>
</head>
<body>
  <main class="card">
    <div class="brand">
      <p class="brand-name">vellers</p>
      <p class="brand-tagline">Fine Jewelry Atelier</p>
    </div>
    <svg class="wordmark" viewBox="0 0 980 554" role="img" aria-label="KOVA!">
      <text class="wordmark-text" x="44" y="470" textLength="892" lengthAdjust="spacing">KOVA!</text>
      <rect class="accent base-rule" x="44" y="510" width="892" height="10"/>
    </svg>
  </main>
</body>
</html>
```